Website for steady harbor detailing.

Need a homepage, pages for: car and truck detailing, boat detailing, airplane detailing, about us, contact us. I have the domain name through nimbushelm so I will need the design uploaded on my domain. Also hoping to link other domains to this page.I would like to see the logo more pronounced. I would like to see a large phone number link to call my business. The layout looks nice but the pics need to depict car washing and waxing not car mechanics. i would like the colors of the webpage to incorporate the colors found in the logo in some way. I would like links to social media pages
Updates

Target Market(s)

Local customers in Vero Beach, Florida.

Number of Pages Required

5+ page

Colors

Requirements
Must have
• Easy to navigate, attractive pages with pictures and logo, professional looking. must have my phone number and logo very prevalent and links to call or go to home page. I would like links to my social media accounts on the home page.
Nice to have
• Easy to navigate, attractive pages with pictures and logo, professional looking.

```html
<!DOCTYPE html>
<html lang="en">
<head>
<meta charset="utf-8">
<title>Steady Harbor Detailing</title>
<link href="https://fonts.googleapis.com/css2?family=Montserrat:wght@600;700&family=Lato:wght@400;700&display=swap" rel="stylesheet">
<style>
:root{
  --red:#ed1c24;
  --navy:#2b2e83;
  --sky:#00a9e6;
  --card:#f2f2f2;
  --body:#555;
  --white:#fff;
}
*{box-sizing:border-box;margin:0;padding:0}
html,body{width:720px;height:1200px;overflow:hidden;background:var(--white)}
body{font-family:'Lato',sans-serif;position:relative}
.topbar{position:absolute;top:0;left:0;width:720px;height:25px;background:var(--red);color:var(--white);font-size:10.5px;display:flex;align-items:center;justify-content:flex-end;padding-right:50px;gap:5px}
.topbar .dot{width:17px;height:17px;border-radius:50%;border:1.5px solid var(--white);background:var(--navy)}
.topbar .follow{margin-right:3px}
.topbar .call{margin-left:20px;display:flex;align-items:center;gap:7px}
.topbar .call a{color:var(--white);text-decoration:none;font-size:14px;font-weight:700;letter-spacing:.3px}
.header{position:absolute;top:25px;left:0;width:720px;height:50px;background:var(--white)}
.brand{position:absolute;left:46px;top:-10px;width:158px;height:64px;background:var(--white);display:flex;align-items:center;gap:7px;padding-left:8px;z-index:2}
.brand .mark{width:18px;height:18px;border-radius:50%;background:var(--red);flex:none}
.brand .name{font-family:'Montserrat',sans-serif;font-weight:700;font-size:14px;color:var(--navy);line-height:1.1;display:block}
.brand .tel{display:block;margin-top:2px;font-family:'Montserrat',sans-serif;font-weight:700;font-size:9px;color:var(--navy);letter-spacing:1.2px;text-decoration:none}
.nav{position:absolute;left:214px;top:18px;display:flex;gap:12px;font-size:10.5px;color:var(--navy)}
.nav .active{color:var(--red)}
.search{position:absolute;left:648px;top:12px;width:26px;height:26px;border-radius:50%;border:1.5px solid var(--red)}
.hero{position:absolute;top:75px;left:0;width:720px;height:343px;background:linear-gradient(110deg,#3a4a8a,#2b3478 45%,#34428a 75%,#4a5a95)}
.hero h1{position:absolute;top:83px;left:0;width:720px;text-align:center;font-family:'Montserrat',sans-serif;font-weight:700;font-size:28px;line-height:32px;color:var(--white);text-transform:uppercase}
.hero p{position:absolute;top:150px;left:160px;width:400px;text-align:center;font-size:9.5px;line-height:15px;color:var(--white)}
.btn-red{position:absolute;top:188px;left:304px;width:112px;height:37px;background:var(--red);color:var(--white);font-size:11.5px;display:flex;align-items:center;justify-content:center}
.promo{position:absolute;top:418px;left:0;width:720px;height:76px}
.promo h2{position:absolute;left:73px;top:18px;width:450px;font-family:'Montserrat',sans-serif;font-weight:700;font-size:13px;line-height:19px;color:var(--white);text-transform:uppercase}
.btn-white{position:absolute;left:525px;top:19px;width:125px;height:38px;background:var(--white);color:var(--red);font-size:12px;display:flex;align-items:center;justify-content:center}
.services-title{position:absolute;top:528px;left:0;width:720px;text-align:center;font-family:'Montserrat',sans-serif;font-weight:700;font-size:21px;color:var(--navy)}
.services-title em{font-style:normal;color:var(--sky)}
.card{position:absolute;top:581px;width:200px;height:256px;background:var(--card)}
.card .photo{height:131px}
.card h3{margin:12px 0 0 14px;font-family:'Montserrat',sans-serif;font-weight:700;font-size:14px;color:var(--navy)}
.card p{margin:8px 14px 0;font-size:8.5px;line-height:15px;color:var(--body)}
.card .plus{position:absolute;left:83px;top:239px;width:34px;height:34px;border-radius:50%;background:var(--sky)}
.about{position:absolute;top:893px;left:0;width:720px;height:250px;background:var(--sky);color:var(--white);text-align:center}
.about h2{margin-top:36px;font-family:'Montserrat',sans-serif;font-weight:700;font-size:21px}
.about p{margin:12px auto 0;width:520px;font-size:8.4px;line-height:15px}
.btn-read{position:absolute;left:310px;top:169px;width:100px;height:37px;background:var(--white);color:var(--sky);font-size:12.5px;display:flex;align-items:center;justify-content:center}
.footer{position:absolute;top:1143px;left:0;width:720px;height:57px;background:var(--red);color:var(--white)}
.footer .copy{position:absolute;left:47px;top:18px;font-size:8.5px;line-height:14px}
.footer .copy b{font-weight:700;text-transform:uppercase}
.footer .social{position:absolute;left:305px;top:15px;display:flex;gap:4px}
.footer .social i{width:25px;height:25px;border-radius:50%;border:1.5px solid var(--white);display:block}
.footer .social i:first-child{background:var(--sky)}
.footer .links{position:absolute;right:48px;top:22px;font-size:8.5px}
</style>
</head>
<body>
<div class="topbar">
  <span class="follow">Follow us on</span>
  <span class="dot" role="img" aria-label="Social profile 1"></span>
  <span class="dot" role="img" aria-label="Social profile 2"></span>
  <span class="dot" role="img" aria-label="Social profile 3"></span>
  <span class="call">Call Us Now
    <svg width="13" height="13" viewBox="0 0 24 24"><path fill="#fff" d="M6.6 10.8a15 15 0 0 0 6.6 6.6l2.2-2.2c.3-.3.7-.4 1-.2 1.1.4 2.3.6 3.6.6.6 0 1 .4 1 1V20c0 .6-.4 1-1 1A17 17 0 0 1 3 4c0-.6.4-1 1-1h3.5c.6 0 1 .4 1 1 0 1.3.2 2.5.6 3.6.1.3 0 .7-.2 1z"/></svg>
    <a href="tel:5550142286">555 - 014 - 2286</a></span>
</div>
<header class="header">
  <div class="brand"><i class="mark"></i><span><span class="name">Steady Harbor<br>Detailing</span><a class="tel" href="tel:5550142286">555-014-2286</a></span></div>
  <nav class="nav"><span>Home</span><span>About</span><span class="active">Car and Truck Detailing</span><span>Boat Detailing</span><span>Airplane Detailing</span><span>Contact Us</span></nav>
  <div class="search">
    <svg width="23" height="23" viewBox="0 0 23 23"><circle cx="10" cy="10" r="4.5" fill="none" stroke="#ed1c24" stroke-width="1.3"/><line x1="13.3" y1="13.3" x2="16.5" y2="16.5" stroke="#ed1c24" stroke-width="1.3"/></svg>
  </div>
</header>
<section class="hero" role="img" aria-label="Worker pressure-washing a heavy truck, under a deep blue overlay">
  <h1>All Heavy Steady Harbor<br>Detailing</h1>
  <p>Lorem Ipsum is simply dummy text of the printing and typesetting industry. Lorem Ipsum has been the Print industry's standard dummy text ever since the 1500s,</p>
  <div class="btn-red">CONTACT US</div>
</section>
<section class="promo">
  <svg width="720" height="76" style="position:absolute;left:0;top:0"><polygon points="0,0 720,0 720,38 692,38 672,76 68,76 48,38 0,38" fill="#ed1c24"/></svg>
  <h2>Get first class services for your car,truck,boat and airplane.....</h2>
  <div class="btn-white">GET APPOINMENT</div>
</section>
<h2 class="services-title">Our <em>Services</em></h2>
<article class="card" style="left:46px">
  <div class="photo" role="img" aria-label="Man washing a car windshield with a sponge" style="background:linear-gradient(135deg,#7a8a6a,#5a6e7e 55%,#c9d2d8)"></div>
  <h3>Car and Truck Detailing</h3>
  <p>Lorem Ipsum is simply dummy text of the printing and typesetting industry. Lorem Ipsum has been the industry's standard dummy 1500s.</p>
  <svg class="plus" viewBox="0 0 34 34"><path d="M17 9v16M9 17h16" stroke="#fff" stroke-width="1.5"/></svg>
</article>
<article class="card" style="left:260px">
  <div class="photo" role="img" aria-label="Man scrubbing the deck of a boat" style="background:linear-gradient(160deg,#c8d4dc,#8a98a4 55%,#d8dde0)"></div>
  <h3>Boat Detailing</h3>
  <p>Lorem Ipsum is simply dummy text of the printing and typesetting industry. Lorem Ipsum has been the industry's standard dummy 1500s.</p>
  <svg class="plus" viewBox="0 0 34 34"><path d="M17 9v16M9 17h16" stroke="#fff" stroke-width="1.5"/></svg>
</article>
<article class="card" style="left:474px">
  <div class="photo" role="img" aria-label="Worker polishing the hull of a large boat in a hangar" style="background:linear-gradient(180deg,#e6e8ea,#bfc4c8 60%,#6e6e66)"></div>
  <h3>Airplane Detailing</h3>
  <p>Lorem Ipsum is simply dummy text of the printing and typesetting industry. Lorem Ipsum has been the industry's standard dummy 1500s.</p>
  <svg class="plus" viewBox="0 0 34 34"><path d="M17 9v16M9 17h16" stroke="#fff" stroke-width="1.5"/></svg>
</article>
<section class="about">
  <h2>About Steady Harbor Detailing</h2>
  <p>Lorem Ipsum is simply dummy text of the printing and typesetting industry. Lorem Ipsum has been the industry's standard dummy text ever since the 1500s, when an unknown printer took a galley of type and scrambled it to make a type specimen book. It has survived not only five centuries, but also the leap into electronic typesetting, remaining essentially unchanged. It was popularised in the 1960s with the release of Typeline sheets containing Lorem Ipsum passages, and more recently with desktop publishing software like Pressworks Layout including versions of Lorem Ipsum</p>
  <div class="btn-read">READ MORE</div>
</section>
<footer class="footer">
  <div class="copy"><b>© Steady Harbor Detailing</b><br>2018. All Rights Reserved.</div>
  <div class="social"><i role="img" aria-label="Social profile 1"></i><i role="img" aria-label="Social profile 2"></i><i role="img" aria-label="Social profile 3"></i><i role="img" aria-label="Social profile 4"></i></div>
  <div class="links">Home &nbsp;|&nbsp; About &nbsp;|&nbsp; Services &nbsp;|&nbsp; Contact</div>
</footer>
</body>
</html>
```